Business card por a urban DJ, up scale audience target

Need a sober design, modern, conservative colors but i can consider some options, y play rnb, hip hop, EDM and top40.

Business card for contact and personal info, double sided, use logo attrached please; im 42 so i need a card acording to my age an target audience.

Target Market(s)

Adult people, up scale audience

Industry/Entity Type

Music Download

Contact Information for Business Card

Cel (318) 4207265518 www.lumadrift.com

Requirements
Must have
• open mind
Nice to have
• open mind
Should not have
• DJ

```html
<!DOCTYPE html>
<html lang="en">
<head>
<meta charset="UTF-8">
<title>LUMA — Business Card</title>
<link href="https://fonts.googleapis.com/css2?family=Saira:wght@500;600;800&display=swap" rel="stylesheet">
<style>
  :root {
    --backdrop: #4a5861;
    --card-dark: #58585a;
    --card-mid: #8c8c8e;
    --card-light: #ffffff;
    --mark-grey: #555557;
    --photo-top: #e4e4e4;
    --photo-mid: #9a9a9a;
    --photo-bottom: #161616;
    --ink-white: #ffffff;
  }
  * { margin: 0; padding: 0; box-sizing: border-box; }
  html, body {
    width: 1200px;
    height: 900px;
    overflow: hidden;
    background: var(--backdrop);
    font-family: "Saira", "Arial", sans-serif;
  }
  .sheet {
    width: 1200px;
    height: 900px;
    display: flex;
    flex-direction: column;
    align-items: center;
    justify-content: center;
    gap: 40px;
  }
  .card {
    position: relative;
    width: 700px;
    height: 400px;
    overflow: hidden;
    box-shadow: 0 10px 30px rgba(0, 0, 0, 0.35);
  }
  .card-front { background: var(--card-dark); }
  .front-bands { position: absolute; inset: 0; }
  .brand-name {
    position: absolute;
    left: 50%;
    transform: translateX(-50%);
    font-weight: 800;
    font-size: 96px;
    line-height: 1;
    letter-spacing: 4px;
    color: var(--mark-grey);
  }
  .card-front .brand-name { top: 118px; }

  .card-back { background: var(--photo-bottom); }
  .crowd-photo {
    position: absolute;
    inset: 0;
    background:
      radial-gradient(ellipse 60% 45% at 50% 18%, rgba(255,255,255,0.85), rgba(255,255,255,0) 70%),
      linear-gradient(to bottom, var(--photo-top) 0%, var(--photo-mid) 42%, #3a3a3a 62%, var(--photo-bottom) 100%);
  }
  .card-back .brand-name { top: 36px; font-size: 82px; }
  .genre-rule {
    position: absolute;
    top: 140px;
    left: 50%;
    transform: translateX(-50%);
    width: 200px;
    height: 2px;
    background: var(--mark-grey);
  }
  .genres {
    position: absolute;
    top: 150px;
    width: 100%;
    text-align: center;
    font-weight: 600;
    font-size: 20px;
    letter-spacing: 3px;
    word-spacing: 14px;
    color: var(--mark-grey);
  }
  .contact-list {
    position: absolute;
    top: 262px;
    left: 0;
    width: 100%;
    list-style: none;
    display: flex;
    flex-direction: column;
    align-items: center;
    gap: 14px;
  }
  .contact-item {
    display: flex;
    align-items: center;
    gap: 12px;
    font-weight: 500;
    font-size: 29px;
    letter-spacing: 1.5px;
    color: var(--ink-white);
    line-height: 1;
  }
  .contact-icon { width: 30px; height: 30px; flex: none; }
</style>
</head>
<body>
<main class="sheet">
  <section class="card card-front" aria-label="Card front">
    <svg class="front-bands" width="700" height="400" viewBox="0 0 700 400" aria-hidden="true">
      <polygon points="0,100 700,0 700,20 0,120" fill="var(--card-mid)"/>
      <polygon points="0,120 700,20 700,240 0,340" fill="var(--card-light)"/>
      <polygon points="0,340 700,240 700,262 0,362" fill="var(--card-mid)"/>
    </svg>
    <div class="brand-name">LUMA</div>
  </section>

  <section class="card card-back" aria-label="Card back">
    <div class="crowd-photo" role="img" aria-label="Black and white photo of a concert crowd with raised hands under stage lights"></div>
    <div class="brand-name">LUMA</div>
    <div class="genre-rule"></div>
    <p class="genres">RNB HIPHOP EDM</p>
    <ul class="contact-list">
      <li class="contact-item">
        <svg class="contact-icon" viewBox="0 0 30 30" aria-hidden="true">
          <rect x="9" y="3" width="12" height="24" rx="2" fill="none" stroke="var(--ink-white)" stroke-width="1.8"/>
          <line x1="9" y1="7" x2="21" y2="7" stroke="var(--ink-white)" stroke-width="1.4"/>
          <line x1="9" y1="22" x2="21" y2="22" stroke="var(--ink-white)" stroke-width="1.4"/>
        </svg>
        <span>(318) 420.726.5518</span>
      </li>
      <li class="contact-item">
        <svg class="contact-icon" viewBox="0 0 30 30" aria-hidden="true">
          <circle cx="15" cy="15" r="12" fill="none" stroke="var(--ink-white)" stroke-width="2"/>
          <ellipse cx="15" cy="15" rx="5.5" ry="12" fill="none" stroke="var(--ink-white)" stroke-width="1.6"/>
          <line x1="3" y1="15" x2="27" y2="15" stroke="var(--ink-white)" stroke-width="1.6"/>
        </svg>
        <span>www.lumadrift.com</span>
      </li>
    </ul>
  </section>
</main>
</body>
</html>
```